RWT Fittings Ltd Business Cards

We need a business card with our business logo. We provide window and door installations on high-rises in west coast British Colombia, Canada.

I would like my business information and details on one side of the card, and the other side the company name with logo

Target Market(s)

General Contractors

Industry/Entity Type

Construction

Contact Information for Business Card

one side i want my company name and logo in the dark theme logo that i provided

Requirements
Must have
• Marco Peltieri, 16045518293, RWTFittings@mailbox-demo.com, 1407-5194 Linden Row Burnaby BC, V5H 2K9, Owner & Manager

```html
<!DOCTYPE html>
<html lang="en">
<head>
<meta charset="utf-8">
<title>RWT Fittings Ltd — Business Cards</title>
<link rel="stylesheet" href="https://fonts.googleapis.com/css2?family=Roboto:wght@400;500;700&display=swap">
<style>
  :root {
    --stage: #232323;
    --card-dark: #1e1e22;
    --card-panel: #24262b;
    --accent-blue: #1ea4e0;
    --logo-blue: #4cc2e8;
    --name-grey: #a9abb0;
    --text-light: #e6e7ea;
    --emboss: #2e2f34;
    --photo-deep: #221f1c;
    --photo-mid: #3b3732;
    --photo-light: #57524c;
  }
  * { box-sizing: border-box; margin: 0; padding: 0; }
  html, body { width: 1200px; height: 780px; overflow: hidden; }
  body {
    background: var(--stage);
    font-family: "Roboto", Arial, sans-serif;
    display: flex;
    align-items: center;
    justify-content: center;
    gap: 50px;
  }
  .card {
    position: relative;
    width: 525px;
    height: 300px;
    overflow: hidden;
    box-shadow: 0 18px 40px rgba(0,0,0,0.55);
  }

  /* Contact side */
  .card--contact { background: var(--card-dark); }
  .contact-panel {
    position: absolute;
    left: 0; top: 0;
    width: 250px; height: 300px;
    background: linear-gradient(180deg, var(--card-panel), var(--card-dark));
  }
  .contact-block {
    position: absolute;
    left: 34px; top: 42px;
    color: var(--text-light);
  }
  .holder-name {
    position: relative;
    font-size: 27px;
    font-weight: 700;
    line-height: 1;
    padding-left: 14px;
  }
  .holder-name::before {
    content: "";
    position: absolute;
    left: 0; top: -4px;
    width: 4px; height: 40px;
    background: var(--accent-blue);
  }
  .holder-name .first { color: var(--accent-blue); }
  .holder-name .last { color: var(--name-grey); }
  .holder-role {
    font-size: 13px;
    font-weight: 500;
    margin: 8px 0 14px 14px;
  }
  .holder-address {
    font-size: 13px;
    line-height: 1.45;
    margin: 0 0 10px 14px;
  }
  .contact-line {
    display: flex;
    align-items: center;
    gap: 8px;
    font-size: 13px;
    line-height: 1.5;
  }
  .contact-line svg { width: 12px; height: 12px; flex: none; }
  .brand-mark {
    position: absolute;
    right: 28px; bottom: 30px;
    display: flex;
    align-items: center;
    gap: 12px;
    color: var(--emboss);
    font-size: 30px;
    font-weight: 700;
  }
  .brand-mark .square {
    width: 30px; height: 30px;
    background: var(--emboss);
  }

  /* Brand side */
  .card--brand { background: var(--photo-deep); }
  .brand-backdrop {
    position: absolute; inset: 0;
    background:
      radial-gradient(ellipse at 75% 55%, var(--photo-light) 0%, transparent 55%),
      linear-gradient(120deg, var(--photo-deep) 0%, var(--photo-mid) 60%, var(--photo-deep) 100%);
  }
  .brand-lockup {
    position: absolute;
    inset: 0;
    display: flex;
    align-items: center;
    justify-content: center;
    gap: 14px;
    color: var(--logo-blue);
    font-size: 36px;
    font-weight: 700;
  }
  .brand-lockup .square {
    width: 36px; height: 36px;
    background: var(--logo-blue);
  }
</style>
</head>
<body>
  <section class="card card--contact" aria-label="Contact side">
    <div class="contact-panel"></div>
    <div class="contact-block">
      <h1 class="holder-name"><span class="first">Marco</span> <span class="last">Peltieri</span></h1>
      <p class="holder-role">Owner &amp; Manager</p>
      <p class="holder-address">1407-5194 Linden Row<br>Burnaby BC, V5H 2K9</p>
      <p class="contact-line">
        <svg viewBox="0 0 24 24" aria-hidden="true"><path fill="var(--accent-blue)" d="M6.6 10.8a15.1 15.1 0 0 0 6.6 6.6l2.2-2.2a1 1 0 0 1 1-.25 11.4 11.4 0 0 0 3.6.57 1 1 0 0 1 1 1V20a1 1 0 0 1-1 1A17 17 0 0 1 3 4a1 1 0 0 1 1-1h3.5a1 1 0 0 1 1 1c0 1.25.2 2.45.57 3.57a1 1 0 0 1-.25 1z"/></svg>
        1604 551 8293
      </p>
      <p class="contact-line">
        <svg viewBox="0 0 24 24" aria-hidden="true"><rect x="2" y="5" width="20" height="14" rx="2" fill="var(--accent-blue)"/><path d="M3 6l9 7 9-7" fill="none" stroke="var(--card-dark)" stroke-width="2"/></svg>
        RWTFittings@mailbox-demo.com
      </p>
    </div>
    <div class="brand-mark"><span class="square"></span>RWT Fittings Ltd</div>
  </section>

  <section class="card card--brand" aria-label="Brand side">
    <div class="brand-backdrop" role="img" aria-label="Soft blurred interior photograph in warm dark tones"></div>
    <div class="brand-lockup"><span class="square"></span>RWT Fittings Ltd</div>
  </section>
</body>
</html>
```